Firm Stationery Design

I need a design for stationery, including: Stationery First Page, Stationery Second Sheet, Envelope, Mailing Label for Flat Envelopes, and Business Cards

```html
<!DOCTYPE html>
<html lang="en">
<head>
<meta charset="utf-8">
<title>Harlow Legal LLC — Stationery</title>
<link href="https://fonts.googleapis.com/css2?family=Montserrat:wght@400;500;600;700;800&display=swap" rel="stylesheet">
<style>
  :root{
    --ink:#1c1c1c;
    --black:#1e1e1e;
    --orange:#f5a01c;
    --paper:#ffffff;
    --sheet:#f4f4f4;
    --backdrop:#a3a3a3;
    --backdrop-light:#b3b1b2;
    --muted:#555555;
    --rule:#8a8a8a;
  }
  *{box-sizing:border-box;margin:0;padding:0}
  html,body{width:1200px;height:957px;overflow:hidden}
  body{font-family:"Montserrat",Arial,sans-serif;color:var(--ink);background:var(--backdrop);position:relative}
  .zone-light{position:absolute;left:650px;top:0;width:550px;height:523px;background:var(--backdrop-light)}
  .piece{position:absolute;background:var(--paper);box-shadow:2px 3px 6px rgba(0,0,0,.3)}
  .piece.dark{background:var(--black);color:#fff}

  /* brand lock-up */
  .brand{display:flex;flex-direction:column;align-items:flex-start;font-weight:800;line-height:1.05;color:var(--ink)}
  .brand-square{display:block;background:var(--orange);margin-bottom:.35em;width:1.3em;height:1.3em}
  .brand-name{display:block;letter-spacing:.02em}
  .dark .brand{color:#fff}

  /* contact block */
  .address{font-size:var(--fs,4px);line-height:1.35;color:var(--ink);border-left:.8px solid var(--orange);padding-left:5px}
  .dark .address{color:#fff;border:0;padding:0}
  .contact-line{display:flex;align-items:center;gap:3px}
  .icon{width:.9em;height:.9em;flex:none}

  /* business cards */
  .card-front{left:76px;top:77px;width:167px;height:95px;border-radius:5px;display:flex;align-items:center;justify-content:center}
  .card-back{left:76px;top:185px;width:167px;height:95px;border-radius:5px;padding:8px 6px 6px 8px}
  .card-back .brand{font-size:8px}
  .card-holder{position:absolute;right:6px;top:8px;text-align:right}
  .card-holder .name{font-size:7.5px;font-weight:700;color:var(--orange)}
  .card-holder .role{font-size:4.8px;color:#fff}
  .card-holder::after{content:"";position:absolute;right:-5px;top:1px;width:3px;height:10px;background:var(--orange)}
  .card-back .address{position:absolute;left:8px;bottom:6px;--fs:4.6px}
  .card-accent{position:absolute;right:0;bottom:0;width:62px;height:60px;background:linear-gradient(135deg,#111 0%,#3a3a3a 60%,#9a9a9a 100%);border-bottom-right-radius:5px}

  /* letterhead */
  .letterhead{left:257px;top:78px;width:142px;height:200px;padding:9px 12px}
  .letterhead .brand{font-size:5.5px}
  .letterhead .address{position:absolute;right:12px;top:10px;--fs:2.6px}
  .recipient{margin-top:24px;font-size:2.6px;line-height:1.4}
  .recipient strong{font-weight:600}
  .body-copy{margin-top:12px;font-size:2.4px;line-height:1.55;color:var(--muted);text-align:justify}
  .body-copy p{margin-bottom:5px}
  .signoff{margin-top:12px;font-size:2.4px;color:var(--muted)}
  .signoff .sign-line{display:block;width:18px;height:6px;border-bottom:.6px solid var(--ink);margin:2px 0}

  /* envelopes */
  .env-back{left:412px;top:79px;width:209px;height:91px;padding:8px 9px}
  .env-back .brand{font-size:5.2px}
  .env-back .address{position:absolute;left:40px;top:9px;--fs:3px}
  .env-flap{left:409px;top:184px;width:210px;height:93px;overflow:hidden}
  .env-flap svg{position:absolute;left:0;top:0}
  .env-flap .brand{position:absolute;left:88px;top:8px;font-size:6px;color:#fff}

  /* notebook */
  .notebook-cover{left:76px;top:309px;width:142px;height:200px;display:flex;align-items:center;justify-content:center}
  .notebook-cover .brand{font-size:16px}
  .notebook-spread{left:302px;top:311px;width:280px;height:197px;background:var(--sheet);display:flex}
  .page{flex:1;padding:9px 7px;position:relative}
  .page+.page{border-left:3px dotted #333}
  .page .brand{font-size:4.8px}
  .page .date{position:absolute;right:7px;top:14px;font-size:4px}
  .page .lines{margin-top:8px;height:150px;background:repeating-linear-gradient(to bottom,transparent 0,transparent 7.3px,#555 7.3px,#555 8px)}

  /* folder */
  .folder-outside{left:746px;top:86px;width:420px;height:190px;display:flex;overflow:hidden}
  .folder-front{flex:1;background:var(--paper);padding:24px 22px;position:relative}
  .folder-front .brand{font-size:20px}
  .folder-front .address{position:absolute;left:22px;bottom:16px;--fs:5px}
  .folder-front .office{position:absolute;right:16px;bottom:16px;font-size:5px;text-align:right;line-height:1.35}
  .folder-back{flex:1;background:var(--black);display:flex;align-items:center;justify-content:center}
  .folder-back-square{width:80px;height:80px;background:var(--orange)}
  .folder-inside{left:746px;top:300px;width:420px;height:180px;display:flex;background:#ececec;overflow:hidden}
  .folder-panel{flex:1;position:relative}
  .folder-panel+.folder-panel{border-left:1px solid #cfcfcf}
  .pocket-left{position:absolute;left:0;bottom:0;width:100%;height:52px;background:var(--black);clip-path:polygon(0 20%,85% 0,100% 20%,100% 100%,0 100%)}
  .pocket-right{position:absolute;left:0;bottom:0;width:100%;height:62px;background:var(--orange);clip-path:polygon(0 20%,95% 0,100% 100%,0 100%)}
  .inserted-sheet{position:absolute;left:34px;top:12px;width:130px;height:150px;background:var(--paper);padding:8px;box-shadow:0 1px 3px rgba(0,0,0,.2)}
  .inserted-sheet .brand{font-size:4.5px}
  .text-bars{margin-top:16px;height:60px;background:repeating-linear-gradient(to bottom,#c4c4c4 0,#c4c4c4 1px,transparent 1px,transparent 4px)}

  /* large envelope */
  .env-large{left:78px;top:586px;width:356px;height:268px;padding:24px 28px}
  .env-large .brand{font-size:13px}
  .env-large .address{position:absolute;left:98px;top:24px;--fs:9px;padding-left:8px}

  /* second sheet */
  .second-sheet{left:480px;top:586px;width:198px;height:264px;padding:16px 16px}
  .second-sheet .brand{font-size:10px}
  .second-sheet .address{position:absolute;left:66px;top:16px;--fs:6.8px;padding-left:6px}

  /* mailing label */
  .label{left:811px;top:571px;width:275px;height:130px;display:flex;align-items:center;justify-content:center}
  .label .brand{font-size:20px;align-items:center}

  /* compliment slip */
  .slip{left:808px;top:734px;width:275px;height:130px;padding:16px 10px}
  .slip .brand{font-size:15px}
  .slip .address{position:absolute;right:10px;top:30px;--fs:5.4px;border:0;padding:0}
  .slip .compliments{position:absolute;right:12px;bottom:10px;font-size:10.5px;font-weight:400}
  .slip .compliments span{color:var(--orange)}
</style>
</head>
<body>
  <div class="zone-light"></div>

  <!-- Business card, front -->
  <section class="piece dark card-front">
    <div class="brand" style="font-size:11px"><span class="brand-square"></span><span class="brand-name">HARLOW<br>LEGAL LLC</span></div>
  </section>

  <!-- Business card, back -->
  <section class="piece dark card-back">
    <div class="brand"><span class="brand-square"></span><span class="brand-name">HARLOW<br>LEGAL LLC</span></div>
    <div class="card-holder"><div class="name">DANIEL REYES</div><div class="role">Managing Director</div></div>
    <div class="card-accent"></div>
    <div class="address">
      <div>Your address, City</div><div>State, Zip 1234</div>
      <div style="height:3px"></div>
      <div class="contact-line"><svg class="icon" viewBox="0 0 10 10"><path d="M2 1h2l1 2-1.2 1a5 5 0 0 0 2.2 2.2L7 5l2 1v2a1 1 0 0 1-1 1A7 7 0 0 1 1 2a1 1 0 0 1 1-1z" fill="var(--orange)"/></svg>123 456 789</div>
      <div class="contact-line"><svg class="icon" viewBox="0 0 10 10"><rect x="1" y="2" width="8" height="6" fill="var(--orange)"/><path d="M1 2l4 3 4-3" stroke="#1e1e1e" stroke-width=".8" fill="none"/></svg>info@harlowlegal.com</div>
      <div class="contact-line"><svg class="icon" viewBox="0 0 10 10"><circle cx="5" cy="5" r="4" fill="var(--orange)"/></svg>www.harlowlegal.com</div>
    </div>
  </section>

  <!-- Letterhead, first page -->
  <section class="piece letterhead">
    <div class="brand"><span class="brand-square"></span><span class="brand-name">HARLOW<br>LEGAL LLC</span></div>
    <div class="address">
      <div>Your address, City</div><div>State, Zip 1234</div>
      <div>123 456 789</div><div>info@harlowlegal.com</div><div>www.harlowlegal.com</div>
    </div>
    <div class="recipient"><strong>MARINA OSTROVA</strong><br>Chief Executive Officer<br>City/State, Zip Code</div>
    <div class="body-copy">
      <p>We write to confirm receipt of your documents and to outline the next steps in your matter. Our team will review each item carefully and contact you within five business days.</p>
      <p>Please keep this letter for your records. If any detail appears incorrect, let us know so we can update our file promptly.</p>
      <p>Thank you for choosing our firm. We look forward to working with you.</p>
    </div>
    <div class="signoff">Sincerely,<span class="sign-line"></span>Peter Lind</div>
  </section>

  <!-- Envelope, back -->
  <section class="piece env-back">
    <div class="brand"><span class="brand-square"></span><span class="brand-name">HARLOW<br>LEGAL LLC</span></div>
    <div class="address"><div>Your address, City</div><div>State, Zip 1234</div></div>
  </section>

  <!-- Envelope, flap side -->
  <section class="piece env-flap">
    <svg width="210" height="93" viewBox="0 0 210 93" aria-hidden="true"><path d="M0 0H210L203 28Q200 34 192 34H18Q10 34 7 28Z" fill="var(--black)"/></svg>
    <div class="brand"><span class="brand-name">HARLOW<br>LEGAL LLC</span></div>
  </section>

  <!-- Notebook cover -->
  <section class="piece dark notebook-cover">
    <div class="brand"><span class="brand-square"></span><span class="brand-name">HARLOW<br>LEGAL LLC</span></div>
  </section>

  <!-- Notebook pages -->
  <section class="piece notebook-spread">
    <div class="page">
      <div class="brand"><span class="brand-square"></span><span class="brand-name">HARLOW<br>LEGAL LLC</span></div>
      <div class="date">Date......./......./.......</div>
      <div class="lines"></div>
    </div>
    <div class="page">
      <div class="brand"><span class="brand-square"></span><span class="brand-name">HARLOW<br>LEGAL LLC</span></div>
      <div class="date">Date......./......./.......</div>
      <div class="lines"></div>
    </div>
  </section>

  <!-- Presentation folder, outside -->
  <section class="piece folder-outside">
    <div class="folder-front">
      <div class="brand"><span class="brand-square"></span><span class="brand-name">HARLOW<br>LEGAL LLC</span></div>
      <div class="address" style="border:0;padding:0">
        <div>123 456 789</div><div>info@harlowlegal.com</div><div>www.harlowlegal.com</div>
      </div>
      <div class="office">Your address, City<br>State, Zip 1234</div>
    </div>
    <div class="folder-back"><div class="folder-back-square"></div></div>
  </section>

  <!-- Presentation folder, inside -->
  <section class="piece folder-inside">
    <div class="folder-panel"><div class="pocket-left"></div></div>
    <div class="folder-panel">
      <div class="inserted-sheet">
        <div class="brand"><span class="brand-square"></span><span class="brand-name">HARLOW<br>LEGAL LLC</span></div>
        <div class="text-bars"></div>
      </div>
      <div class="pocket-right"></div>
    </div>
  </section>

  <!-- Large envelope -->
  <section class="piece env-large">
    <div class="brand"><span class="brand-square"></span><span class="brand-name">HARLOW<br>LEGAL LLC</span></div>
    <div class="address"><div>Your address, City</div><div>State, Zip 1234</div></div>
  </section>

  <!-- Stationery, second sheet -->
  <section class="piece second-sheet">
    <div class="brand"><span class="brand-square"></span><span class="brand-name">HARLOW<br>LEGAL LLC</span></div>
    <div class="address"><div>Your address, City</div><div>State, Zip 1234</div></div>
  </section>

  <!-- Mailing label -->
  <section class="piece label">
    <div class="brand"><span class="brand-square"></span><span class="brand-name" style="text-align:center">HARLOW<br>LEGAL LLC</span></div>
  </section>

  <!-- Compliment slip -->
  <section class="piece slip">
    <div class="brand"><span class="brand-square"></span><span class="brand-name">HARLOW<br>LEGAL LLC</span></div>
    <div class="address">
      <div>Your address, City</div><div>State, Zip 1234</div>
      <div style="height:4px"></div>
      <div class="contact-line"><svg class="icon" viewBox="0 0 10 10"><path d="M2 1h2l1 2-1.2 1a5 5 0 0 0 2.2 2.2L7 5l2 1v2a1 1 0 0 1-1 1A7 7 0 0 1 1 2a1 1 0 0 1 1-1z" fill="var(--orange)"/></svg>123 456 789</div>
      <div class="contact-line"><svg class="icon" viewBox="0 0 10 10"><rect x="1" y="2" width="8" height="6" fill="var(--orange)"/><path d="M1 2l4 3 4-3" stroke="#fff" stroke-width=".8" fill="none"/></svg>info@harlowlegal.com</div>
      <div class="contact-line"><svg class="icon" viewBox="0 0 10 10"><circle cx="5" cy="5" r="4" fill="var(--orange)"/></svg>www.harlowlegal.com</div>
    </div>
    <div class="compliments">with <span>compliments</span></div>
  </section>
</body>
</html>
```